Oil and Gas Exploration and Production company needs a business card design

We need a business card design using our logo and colors in the logo. We want a mainstream design.

```html
<!DOCTYPE html>
<html lang="en">
<head>
<meta charset="UTF-8">
<title>Sorel Oil &amp; Gas – Business Card</title>
<link rel="stylesheet" href="https://fonts.googleapis.com/css2?family=Work+Sans:wght@400;500;700&display=swap">
<style>
  :root {
    --backdrop: #dfe5ec;
    --card: #f3f5f7;
    --ink: #2b2b2d;
    --ink-soft: #4a4c50;
    --gold: #b08a2e;
    --gold-deep: #a27a22;
    --shadow: rgba(30, 40, 55, 0.18);
  }
  * { box-sizing: border-box; margin: 0; padding: 0; }
  html, body {
    width: 1200px;
    height: 900px;
    overflow: hidden;
    background: var(--backdrop);
    font-family: "Work Sans", sans-serif;
  }
  .business-card {
    position: absolute;
    left: 100px;
    top: 167px;
    width: 1000px;
    height: 567px;
    background: var(--card);
    box-shadow: 0 18px 40px var(--shadow);
    overflow: hidden;
  }
  .brand {
    position: absolute;
    left: 44px;
    top: 60px;
    display: flex;
    align-items: center;
    gap: 16px;
  }
  .brand-dot {
    width: 44px;
    height: 44px;
    border-radius: 50%;
    background: var(--ink);
  }
  .brand-name {
    font-size: 52px;
    font-weight: 700;
    color: var(--ink);
    letter-spacing: -0.5px;
  }
  .holder {
    position: absolute;
    left: 44px;
    top: 250px;
  }
  .holder-name {
    font-size: 41px;
    font-weight: 500;
    color: var(--gold);
    line-height: 1.1;
  }
  .holder-role {
    font-size: 21px;
    color: var(--ink);
    margin-top: 6px;
  }
  .address {
    position: absolute;
    left: 44px;
    top: 348px;
    font-size: 22px;
    line-height: 1.45;
    color: var(--ink-soft);
    font-style: normal;
  }
  .contacts {
    position: absolute;
    left: 44px;
    top: 436px;
    list-style: none;
    font-size: 22px;
    line-height: 1.4;
    color: var(--ink);
  }
  .contacts li {
    display: flex;
    align-items: center;
    gap: 10px;
  }
  .contacts svg { width: 16px; height: 16px; flex: none; }
  .emblem {
    position: absolute;
    left: 476px;
    top: 40px;
    width: 480px;
    height: 480px;
  }
</style>
</head>
<body>
  <section class="business-card" aria-label="Sorel Oil &amp; Gas business card">
    <div class="brand">
      <span class="brand-dot"></span>
      <span class="brand-name">Sorel Oil &amp; Gas</span>
    </div>

    <div class="holder">
      <h1 class="holder-name">Dale Hartwell</h1>
      <p class="holder-role">CFO</p>
    </div>

    <address class="address">2450 Ridgeline Ave,<br>Abilene, Texas us</address>

    <ul class="contacts">
      <li>
        <svg viewBox="0 0 16 16" aria-hidden="true"><path d="M4 1.5l2.4 3-1.3 1.6a8 8 0 0 0 4.8 4.8l1.6-1.3 3 2.4-1.3 2.2C8 14 2 8 1.8 2.8z" fill="none" stroke="#a27a22" stroke-width="1.4" stroke-linejoin="round"/></svg>
        (555) 014-2280
      </li>
      <li>
        <svg viewBox="0 0 16 16" aria-hidden="true"><rect x="1.5" y="3.5" width="13" height="9" fill="none" stroke="#a27a22" stroke-width="1.4"/><path d="M1.5 3.5L8 9l6.5-5.5" fill="none" stroke="#a27a22" stroke-width="1.4"/></svg>
        info@sorelenergy.com
      </li>
      <li>
        <svg viewBox="0 0 16 16" aria-hidden="true"><circle cx="8" cy="8" r="6.3" fill="none" stroke="#a27a22" stroke-width="1.4"/><path d="M1.7 8h12.6M8 1.7c-3 3.5-3 9.1 0 12.6M8 1.7c3 3.5 3 9.1 0 12.6" fill="none" stroke="#a27a22" stroke-width="1.2"/></svg>
        www.sorelenergy.com
      </li>
    </ul>

    <svg class="emblem" viewBox="0 0 480 480" aria-hidden="true">
      <circle cx="240" cy="240" r="100" fill="none" stroke="var(--gold-deep)" stroke-width="26" opacity="0.9"/>
    </svg>
  </section>
</body>
</html>
```